KTWG application splash screen

We need a 1024x768 image for use as an application splash screen.
The image will be displayed full screen on an 10 inch industrial PC 1024x768 screen while our application is launching. The image should convey that the application is "Waiting for connection to Wi-Fi access point..." and include a graphic of the industrial PC connected to the access point via an Ethernet cable. A list of troubleshooting steps should be included at the bottom of the image. The troubleshooting steps should not be the main focus of the image and should be shown in a smaller font (but still readable at 1024x768 displayed on a 10 inch screen).
I will include a mock up of the general idea of what we are looking for as well as image files for the industrial PC, a screenshot of our application to show on the PC's screen and the AP.
For general look and feel and a sense of corporate branding please review our website https://marrowgatesoilworks.example/. The splash screen should reflect corporate branding.
Target Market(s)
Users of our application
Industry/Entity Type
Agriculture
Look and feel

```html
<!DOCTYPE html>
<html lang="en">
<head>
<meta charset="utf-8">
<title>KTWG – Waiting for Wi-Fi</title>
<link rel="stylesheet" href="https://fonts.googleapis.com/css2?family=Barlow:wght@500;600&family=Open+Sans:wght@400;600&display=swap">
<style>
  :root {
    --brand-green: #2bb673;
    --brand-green-dark: #1f9a5e;
    --paper: #ffffff;
    --device-dark: #2a2b2d;
    --device-edge: #111214;
    --ap-white: #f1f3f2;
    --ap-shade: #d4d8d6;
    --cable: #1b1b1b;
  }
  * { box-sizing: border-box; margin: 0; padding: 0; }
  html, body { width: 1200px; height: 900px; overflow: hidden; background: var(--paper); }
  .splash { position: relative; width: 1200px; height: 900px; overflow: hidden; background: var(--paper); font-family: "Open Sans", sans-serif; }
  .backdrop { position: absolute; inset: 0; }
  .title {
    position: absolute; left: 40px; top: 38px; width: 730px;
    color: var(--paper); font-family: "Barlow", sans-serif; font-weight: 500;
    font-size: 74px; line-height: 82px; text-align: center;
  }
  .device-computer {
    position: absolute; left: 91px; top: 387px; width: 316px; height: 252px;
    border-radius: 16px; background: linear-gradient(160deg, var(--device-dark), var(--device-edge));
  }
  .device-access-point {
    position: absolute; left: 1000px; top: 146px; width: 76px; height: 405px;
    border-radius: 22px 22px 10px 10px;
    background: linear-gradient(90deg, var(--ap-shade), var(--ap-white) 45%, var(--ap-shade));
  }
  .label { position: absolute; font-family: "Barlow", sans-serif; font-weight: 500; text-align: center; }
  .label-computer { left: 118px; top: 646px; width: 260px; font-size: 22px; color: var(--brand-green); }
  .label-ap { left: 945px; top: 618px; width: 180px; font-size: 20px; line-height: 24px; color: var(--paper); }
  .troubleshooting { position: absolute; left: 91px; top: 712px; width: 800px; color: var(--paper); }
  .troubleshooting h2 { font-size: 13.5px; font-weight: 600; margin-bottom: 8px; }
  .steps { list-style: none; font-size: 13.5px; line-height: 18px; }
  .steps li { position: relative; padding-left: 20px; }
  .steps li::before { content: "➤"; position: absolute; left: 0; }
  .substeps { list-style: none; }
  .substeps li::before { content: "➡"; font-size: 11px; }
  .brand-tile {
    position: absolute; left: 947px; top: 701px; width: 171px; height: 171px;
    border-radius: 38px; background: var(--brand-green);
    display: flex; align-items: center; justify-content: center;
    color: var(--paper); font-family: "Barlow", sans-serif; font-weight: 600; font-size: 44px;
  }
</style>
</head>
<body>
<main class="splash">
  <svg class="backdrop" width="1200" height="900" viewBox="0 0 1024 768" aria-hidden="true">
    <path fill="var(--brand-green)" d="M0 0 H1024 V70 H860 C790 70 750 110 700 170 C650 235 610 268 540 268 H0 Z"/>
    <path fill="var(--brand-green)" d="M806 180 A75 75 0 0 1 881 105 H960 V768 H806 Z"/>
    <path fill="var(--brand-green)" d="M0 594 H710 A50 50 0 0 1 760 644 V768 H0 Z"/>
    <rect x="786" y="582" width="192" height="180" rx="46" fill="var(--paper)"/>
    <path fill="none" stroke="var(--cable)" stroke-width="4" d="M347 512 H870 Q885 512 885 497 V470"/>
  </svg>

  <h1 class="title">Waiting for<br>connection to Wi-Fi<br>access point...</h1>

  <div class="device-computer" role="img" aria-label="Industrial tablet computer showing the seeding application screen"></div>
  <p class="label label-computer">Tractor Cab Computer</p>

  <div class="device-access-point" role="img" aria-label="White outdoor Wi-Fi access point with two antennas"></div>
  <p class="label label-ap">Wi-Fi Access<br>Point</p>

  <section class="troubleshooting">
    <h2>Troubleshooting steps:</h2>
    <ul class="steps">
      <li>This screen should only be visible for a short time on boot.</li>
      <li>If this screen stays visible for more than a minute:
        <ul class="substeps">
          <li>Verify that the Wi-Fi Access Point (AP) powers up when this system does (indicated by a green light on the side of the AP).</li>
          <li>Check the Ethernet cable between this system and the AP for damage, and replace it if necessary.</li>
          <li>Power-cycle this system and wait for it to reboot fully.</li>
          <li>If the issue persists, contact KTWG support for further assistance.</li>
        </ul>
      </li>
    </ul>
  </section>

  <div class="brand-tile">KTWG</div>
</main>
</body>
</html>
```